Professional Services - letterhead / business cards

The company (velmora partners) will provide services to Investment Funds and large investors in Spain. I have recently chosen a logo that I am attaching.

I would like a simple stationary design that i could use as letter head, business cards and "with compliments" cards.

I am not quite sure which color I will mostly use for the logo, in the email signature I will probably lean towards the white background and grey letters. I am attaching my favourite options.

Target Market(s)

Large Multinationals, Investment funds and Law firms

Industry/Entity Type

Business

Requirements
Must have
• my details are:
Luis R. Abadal
Velmora Partners S.L.
Casa de Torrelumbre
Calle de Vientoalto 27
28014 Madrid
T: +34 (91) 387-2265
M: +34 (646) 819-054
e-mail: labadal@velmorapartners.com

```html
<!DOCTYPE html>
<html lang="es">
<head>
<meta charset="utf-8">
<title>Velmora Partners – Business Cards</title>
<link href="https://fonts.googleapis.com/css2?family=Questrial&display=swap" rel="stylesheet">
<style>
  :root {
    --navy: #17197f;
    --navy-deep: #101266;
    --grey: #b9bbc2;
    --grey-text: #8a8c94;
    --white: #ffffff;
    --backdrop: #e9e7e3;
    --font: "Questrial", "Century Gothic", sans-serif;
  }
  * { box-sizing: border-box; margin: 0; padding: 0; }
  html, body {
    width: 1200px;
    height: 588px;
    overflow: hidden;
    background: var(--backdrop);
    font-family: var(--font);
  }
  .canvas {
    position: relative;
    width: 1200px;
    height: 588px;
  }
  .card {
    position: absolute;
    top: 126px;
    width: 520px;
    height: 336px;
    border-radius: 16px;
    overflow: hidden;
    box-shadow: 0 6px 18px rgba(0,0,0,0.18);
  }

  /* Front: navy card */
  .card--front {
    left: 50px;
    background: var(--navy);
    color: var(--white);
    display: flex;
    flex-direction: column;
    align-items: center;
    justify-content: center;
  }
  .card--front .brand-name {
    font-size: 44px;
    letter-spacing: 0.5px;
  }
  .card--front .website {
    margin-top: 22px;
    font-size: 13px;
    letter-spacing: 3.2px;
  }

  /* Back: white card with contact details */
  .card--back {
    left: 630px;
    background: var(--white);
    color: var(--navy);
  }
  .card--back .brand-name {
    position: absolute;
    top: 38px;
    left: 52px;
    font-size: 38px;
    color: var(--navy);
  }
  .holder {
    position: absolute;
    top: 104px;
    left: 52px;
  }
  .holder-name {
    font-size: 19px;
    letter-spacing: 1px;
    text-transform: uppercase;
  }
  .holder-company {
    font-size: 12px;
    font-style: italic;
    color: var(--grey-text);
    margin-top: 2px;
  }
  .contacts {
    position: absolute;
    top: 158px;
    left: 52px;
    font-size: 12.5px;
    color: var(--grey-text);
    line-height: 21px;
  }
  .contact-row { display: flex; align-items: center; gap: 22px; }
  .contact-item { display: flex; align-items: center; gap: 7px; }
  .contact-label {
    display: inline-flex;
    align-items: center;
    justify-content: center;
    width: 15px;
    height: 15px;
    border-radius: 50%;
    background: #d6d7db;
    color: var(--white);
    font-size: 9px;
  }
  .swoosh {
    position: absolute;
    left: 0;
    bottom: 0;
    width: 520px;
    height: 336px;
  }
  .address {
    position: absolute;
    right: 26px;
    bottom: 20px;
    text-align: right;
    color: var(--white);
    font-size: 13.5px;
    line-height: 20px;
  }
</style>
</head>
<body>
<main class="canvas">

  <section class="card card--front" aria-label="Business card front">
    <p class="brand-name">velmora partners</p>
    <p class="website">www.velmorapartners.com</p>
  </section>

  <section class="card card--back" aria-label="Business card back">
    <svg class="swoosh" viewBox="0 0 520 336" aria-hidden="true">
      <path d="M0,196 Q240,300 520,228 L520,244 Q240,300 0,214 Z" fill="var(--grey)"/>
      <path d="M0,220 Q240,302 520,250 L520,336 L0,336 Z" fill="var(--navy)"/>
    </svg>

    <p class="brand-name">velmora partners</p>

    <div class="holder">
      <p class="holder-name">Luis R. Abadal</p>
      <p class="holder-company">Velmora Partners S.L.</p>
    </div>

    <div class="contacts">
      <div class="contact-row">
        <span class="contact-item"><span class="contact-label">P</span>+34 (91) 387-2265</span>
        <span class="contact-item"><span class="contact-label">C</span>+34 (646) 819-054</span>
      </div>
      <div class="contact-row">
        <span class="contact-item"><span class="contact-label">E</span>labadal@velmorapartners.com</span>
      </div>
    </div>

    <address class="address" style="font-style: normal;">
      Casa de Torrelumbre<br>
      Calle de Vientoalto 27, 28014 Madrid
    </address>
  </section>

</main>
</body>
</html>
```